Webdesign für Comic Shop
Zielgruppe
Webdesign: Jugendliche und junge Erwachsene zwischen 14 & 25 Jahren; Manga - Card Game - Comic und Anime Fans
Shop: Auch für Comic Händler & Großhändler ansprechend, einfach strukturiert aber trotzdem modern und eine fröhliche Farbgestaltung
Mobile Website: jugendlich
Flyer: für jugendliche
Aufgabenstellung
Designt werden sollen folgende Komponenten:
(1) webdesign für Comicshop mit 5 Filialen, gegliedert in "Home" und die Unterseiten der Filialen; Startseite plus eine Unterseite, Inhalte: Bilder unserer Filialen und unseres Teams, Events in unseren Shops, Vorstellung unseres Sortimentes, Blog was so los ist auf dem Comic Markt, Name HEFTE INSEL, Newsletter, Facebook - Twitter - RSS Button; Bilder von Events
(2) Mobile Website
Htlm5 website, die über Android oder iPhone Browser zu erreichen ist; Home: alle 5 Filialen als Button zum anklicken; Untermenüpunkt 1 - 1. Filiale - Untermenüpunkt 2 - 2. Filiale usw; in den einzelnen Filialen ein Button mit "Events" und "Kontakt" und "Bilder", unter dem Button "Kontakt" ein Button mit der Telefonnummer, die man direkt anwählen kann
(3) Shop
passend zum webdesign mit Händleranbindung, der Shop basiert auf der Grundlage von http://www.kassolino.de/; das design soll sich eng am kassolino-demo-shop orientieren; für die Artikellieferbarkeiten bitte das "Comicmännchen" unseres Logos verwenden mit verschiedenen Posen für "lieferbar" - "noch geringe Mengen lieferbar" - "ausverkauft" - "Neuheit" - "bald lieferbar";
(4) Logoumgestaltung
Ein Vorschlag liegt von uns vor, der professionel als LOGO gestaltet werden soll - Farbgestaltung: 4farbig, Photoshop Vektor Datei, grelles grün, kräftiges blau, schwarz, weiss

```html
<!DOCTYPE html>
<html lang="de">
<head>
<meta charset="utf-8">
<title>HEFTE INSEL – Mobile</title>
<link rel="stylesheet" href="https://fonts.googleapis.com/css2?family=PT+Sans:wght@400;700&display=swap">
<style>
  :root {
    --page-bg: #0c0d0f;
    --space-deep: #050a18;
    --space-mid: #0f2a5c;
    --planet-glow: #2f7fd0;
    --planet-light: #8cc4f2;
    --logo-ink: #eaf4ff;
    --btn-top: #5d6874;
    --btn-bottom: #2c333c;
    --btn-edge: #1a1e23;
    --btn-accent: #9fd0f5;
    --btn-text: #ffffff;
    --footer-text: #e6e9ee;
  }
  * { margin: 0; padding: 0; box-sizing: border-box; }
  html, body {
    width: 927px; height: 1200px; overflow: hidden;
    background: var(--page-bg);
    font-family: "PT Sans", Arial, sans-serif;
  }
  .screen {
    position: relative; width: 927px; height: 1200px;
    background:
      radial-gradient(circle at 50% 60%, #15171b 0%, var(--page-bg) 70%);
  }
  .hero {
    position: absolute; left: 0; top: 0; width: 927px; height: 425px;
    background:
      radial-gradient(ellipse 90% 55% at 50% 105%, var(--planet-light) 0%, var(--planet-glow) 30%, var(--space-mid) 58%, transparent 75%),
      linear-gradient(180deg, var(--space-deep) 0%, #0a1838 60%, var(--space-mid) 100%);
    border-bottom: 3px solid #1b1f25;
  }
  .mascot-area {
    position: absolute; left: 340px; top: 150px; width: 325px; height: 320px;
    border-radius: 46%;
    background: radial-gradient(circle at 50% 45%, #e3e8ee 0%, #a9b3bf 45%, rgba(120,135,150,0) 72%);
  }
  .brand-name {
    position: absolute; left: 0; right: 0; top: 20px;
    text-align: center;
    font-weight: 700; font-size: 104px; letter-spacing: 4px;
    color: var(--logo-ink);
    line-height: 1;
  }
  .shop-list {
    position: absolute; left: 31px; top: 520px; width: 865px;
    list-style: none;
    display: flex; flex-direction: column; gap: 59px;
  }
  .shop-button {
    display: flex; align-items: center; justify-content: center;
    height: 87px;
    border-radius: 16px;
    border: 2px solid var(--btn-edge);
    background: linear-gradient(180deg, var(--btn-top) 0%, #48525d 45%, var(--btn-bottom) 100%);
    box-shadow: inset 0 2px 0 rgba(255,255,255,0.18);
    font-weight: 700; font-size: 52px; letter-spacing: 1px;
    color: var(--btn-text);
    text-decoration: none;
  }
  .shop-button .label-shop { color: var(--btn-accent); margin-right: 14px; }
  .footer-links {
    position: absolute; left: 0; right: 0; top: 1118px;
    text-align: center;
    font-size: 38px; color: var(--footer-text);
  }
  .footer-links a { color: inherit; text-decoration: none; }
  .footer-links .divider { margin: 0 10px; }
</style>
</head>
<body>
<main class="screen">
  <header class="hero" role="img" aria-label="Weltraumszene mit blau leuchtendem Planeten">
    <div class="mascot-area" role="img" aria-label="Silbernes Comic-Maskottchen mit ausgebreiteten Armen"></div>
    <h1 class="brand-name">HEFTE INSEL</h1>
  </header>

  <ul class="shop-list">
    <li><a class="shop-button" href="#osnabrueck"><span class="label-shop">SHOP</span>IN OSNABRÜCK</a></li>
    <li><a class="shop-button" href="#muenster"><span class="label-shop">SHOP</span>IN MÜNSTER</a></li>
    <li><a class="shop-button" href="#rheine"><span class="label-shop">SHOP</span>IN RHEINE</a></li>
    <li><a class="shop-button" href="#duisburg"><span class="label-shop">SHOP</span>IN DUISBURG</a></li>
  </ul>

  <footer class="footer-links">
    <a href="#hotline">Hotline</a><span class="divider">|</span><a href="#impressum">Impressum</a>
  </footer>
</main>
</body>
</html>
```